Corvane Freight Company Business Card Design

We are a company that delivers natural saltwater (from the ocean) to aquarium companies, restaurants and home marine tanks. I would like a new business card to suit.

Must include Name, company name, abn, contact number and website as well as logo (see attached).

Looking for a design that stands out, has a clean but unique appearance.

Double and single sided entries welcome

Business

• Logo

```html
<!DOCTYPE html>
<html lang="en">
<head>
<meta charset="utf-8">
<title>Corvane Freight Company – Business Card</title>
<link rel="stylesheet" href="https://fonts.googleapis.com/css2?family=Source+Sans+3:wght@400;600&display=swap">
<style>
  :root {
    --backdrop: #161616;
    --card: #ffffff;
    --brand-blue: #1b8fd2;
    --sea-blue: #56c8f0;
    --ink: #1c1c1c;
  }
  * { margin: 0; padding: 0; box-sizing: border-box; }
  html, body {
    width: 1200px;
    height: 420px;
    overflow: hidden;
    background: var(--backdrop);
    font-family: "Source Sans 3", "Myriad Pro", Arial, sans-serif;
  }
  .canvas {
    position: relative;
    width: 1200px;
    height: 420px;
  }
  .card {
    position: absolute;
    top: 65px;
    width: 518px;
    height: 295px;
    background: var(--card);
    text-align: center;
  }
  .card--front { left: 69px; }
  .card--back { left: 621px; }

  .brand {
    position: absolute;
    left: 0;
    width: 100%;
    display: flex;
    flex-direction: column;
    align-items: center;
  }
  .brand-row {
    display: flex;
    align-items: center;
    justify-content: center;
  }
  .brand-dot {
    flex: none;
    border-radius: 50%;
    background: var(--sea-blue);
  }
  .company-name {
    color: var(--brand-blue);
    font-weight: 400;
    letter-spacing: -0.4px;
    white-space: nowrap;
    line-height: 1;
  }
  .tagline {
    color: var(--brand-blue);
    font-weight: 600;
    white-space: nowrap;
    line-height: 1;
  }

  .card--front .brand { top: 62px; }
  .card--front .brand-row { gap: 10px; }
  .card--front .brand-dot { width: 26px; height: 26px; }
  .card--front .company-name { font-size: 32px; }
  .card--front .tagline { font-size: 18px; margin-top: 10px; }

  .card--back .brand { top: 128px; }
  .card--back .brand-row { gap: 12px; }
  .card--back .brand-dot { width: 34px; height: 34px; }
  .card--back .company-name { font-size: 40px; }
  .card--back .tagline { font-size: 24px; margin-top: 12px; }

  .holder-name {
    position: absolute;
    top: 190px;
    left: 0;
    width: 100%;
    font-size: 19px;
    color: var(--brand-blue);
  }
  .contact {
    position: absolute;
    top: 226px;
    left: 0;
    width: 100%;
    font-size: 13px;
    line-height: 21px;
    color: var(--ink);
  }
  .contact-row { display: flex; justify-content: center; align-items: center; gap: 18px; }
  .contact-item { display: inline-flex; align-items: center; gap: 6px; }
  .contact-icon { width: 10px; height: 10px; }
</style>
</head>
<body>
<main class="canvas">
  <section class="card card--front" aria-label="Card front">
    <div class="brand">
      <div class="brand-row">
        <span class="brand-dot" aria-hidden="true"></span>
        <h1 class="company-name">Corvane Freight Company</h1>
      </div>
      <p class="tagline">Saltwater Deliveries</p>
    </div>
    <p class="holder-name">Your Name, Title</p>
    <div class="contact">
      <div class="contact-row">
        <span class="contact-item">
          <svg class="contact-icon" viewBox="0 0 10 10" aria-hidden="true">
            <path d="M2 0.8 L3.6 2.8 L2.8 3.8 Q4 6.2 6.2 7.2 L7.2 6.4 L9.2 8 L8 9.4 Q3.5 9 0.6 2 Z" fill="#1c1c1c"/>
          </svg>
          123-456-7892
        </span>
        <span class="contact-item">
          <svg class="contact-icon" viewBox="0 0 10 10" aria-hidden="true">
            <circle cx="5" cy="5" r="4.3" fill="none" stroke="#1c1c1c" stroke-width="1"/>
            <ellipse cx="5" cy="5" rx="1.8" ry="4.3" fill="none" stroke="#1c1c1c" stroke-width="0.8"/>
            <line x1="0.7" y1="5" x2="9.3" y2="5" stroke="#1c1c1c" stroke-width="0.8"/>
          </svg>
          www.corvanefreight.com
        </span>
      </div>
      <div>Street Name, City Name ,State, Zip Code</div>
      <div>ABN: 123456789</div>
    </div>
  </section>

  <section class="card card--back" aria-label="Card back">
    <div class="brand">
      <div class="brand-row">
        <span class="brand-dot" aria-hidden="true"></span>
        <h2 class="company-name">Corvane Freight Company</h2>
      </div>
      <p class="tagline">Saltwater Deliveries</p>
    </div>
  </section>
</main>
</body>
</html>
```